Restaurant Menu New Design

Hello Designers,

Blue Fern is a casual family oriented dine-in restaurant, we serve American Italian dishes like Pizza, Pasta, and Sandwiches.

We are excited about adding some new delicious dishes and recipes to our menu. And we are looking for a talented and creative designer to design it.

The menu is a 12 page black leather book, page size is:
6.5" X 11.69" (16.51 cm X 29.69 cm)

Below is the scope of work and requirements:

1) Design a completely all new, creative, and beautiful menu, including cover page, blue fern oven intro. page, interior pages, and kids menu page.

2) Design a take out edition of the menu. It will be exactly the same as the dine-in menu, but with the addition of a back cover page with info such as contacts, social media, location map, etc…

3) Files are required in Adobe Illustrator format. Layers should be organized, all text should be editable, and all the food pictures easy to change.

4) This is a two language menu, so you are required to make space in the design for a second language. The easiest way to do that is have every item listed in English twice, then I will edit the second text with Illustrator.

5) In your initial design submission, the minimum you are required to submit are these 4 pages:
– Cover page
– Typical interior menu page
– Kids menu page
– Take-out menu back cover page

If your initial design is selected, then you are required to submit all remaining pages to complete the project.

In the link below, you will find:
1) Logo
2) New menu text in Excel
3) Food images (will take some time to upload)
4) The old dine-in and take out menu designs

https://www.filevaultra.com/sh/kq7tmwzabe3pxd/BBBrTnpLk41QaWmZpQ8V2X7Jd?dl=0

Thank you for stopping by and reading this brief. I hope you like this project and enjoy designing our new menu. Please let me know if you have any questions.

Cheers!

Project Deadline Extended
Reason: We have decided to extend the deadline due to the low number of submissions which was much lower than the expected submissions we were give by Brief Harbor.

```html
<!DOCTYPE html>
<html lang="en">
<head>
<meta charset="utf-8">
<title>Kids Menu</title>
<link href="https://fonts.googleapis.com/css2?family=Open+Sans:wght@300;400;600;700&family=Tajawal:wght@300;400;500&display=swap" rel="stylesheet">
<style>
:root{
  --board:#3a3a3c;
  --chalk:#ffffff;
  --chalk-soft:#c4c4c4;
  --doodle:rgba(255,255,255,0.035);
  --burger-a:#c98a4a;
  --burger-b:#8a2f22;
  --pasta-a:#a4482a;
  --pasta-b:#eae4dc;
  --tender-a:#b6742e;
  --tender-b:#e9c76a;
}
*{margin:0;padding:0;box-sizing:border-box}
html,body{width:1200px;height:2219px;overflow:hidden;background:var(--board)}
.menu-page{position:relative;width:1200px;height:2219px;background:var(--board);font-family:"Open Sans",Arial,sans-serif;color:var(--chalk)}
.frame-lines{position:absolute;left:0;top:0}
.page-title{position:absolute;top:108px;left:0;width:1200px;text-align:center;font-size:38px;font-weight:400;letter-spacing:1px}
.photo{position:absolute}
.photo-burger{left:144px;top:337px;width:529px;height:354px;background:radial-gradient(circle at 52% 50%,var(--burger-b) 0 9%,#e8c48a 10% 45%,var(--burger-a) 70%,#6e2a1c)}
.photo-pasta{left:550px;top:880px;width:527px;height:351px;background:radial-gradient(ellipse at 48% 62%,var(--pasta-a) 0 28%,var(--pasta-b) 30% 52%,#2a1d17 70%)}
.photo-tenders{left:138px;top:1509px;width:528px;height:351px;background:linear-gradient(120deg,var(--tender-a) 0%,#c98f3f 40%,var(--tender-b) 65%,#d8c3a6 100%)}
.doodle{position:absolute;background:var(--doodle);border-radius:50%}
.dish{position:absolute;text-align:center}
.dish-name{font-weight:700;font-size:24px;line-height:31px;text-transform:uppercase}
.dish-name-ar{font-family:"Tajawal",Arial,sans-serif;font-size:25px;line-height:32px;font-weight:400;direction:rtl}
.dish-note{font-weight:300;font-size:21px;line-height:29px;color:var(--chalk-soft)}
.dish-note-ar{font-family:"Tajawal",Arial,sans-serif;font-weight:300;font-size:22px;line-height:30px;color:var(--chalk-soft);direction:ltr}
.dish-note-ar bdi{direction:rtl;unicode-bidi:isolate}
.price{display:inline-block;margin-left:14px;font-family:"Open Sans",Arial,sans-serif;font-weight:300;font-size:21px}
.line{display:block}
.dish-burger{left:700px;top:334px;width:366px}
.dish-pasta{left:140px;top:916px;width:372px}
.dish-tenders{left:700px;top:1532px;width:402px}
</style>
</head>
<body>
<main class="menu-page">
  <svg class="frame-lines" width="1200" height="2219" viewBox="0 0 1200 2219" fill="none" stroke="#ffffff" stroke-width="2.5" aria-hidden="true">
    <line x1="0" y1="138" x2="429" y2="138"/>
    <line x1="784" y1="138" x2="1200" y2="138"/>
    <polyline points="599,268 1102,268 1102,759 326,759 326,872"/>
    <polyline points="286,824 326,872 366,824"/>
    <polyline points="578,289 118,289 118,721 452,721"/>
    <polyline points="92,585 92,740 259,740"/>
    <polyline points="710,863 528,863 528,1036"/>
    <polyline points="1102,932 1102,1270 829,1270"/>
    <polyline points="323,1147 323,1398 910,1398 910,1490"/>
    <polyline points="870,1444 910,1492 950,1444"/>
    <polyline points="326,1477 695,1477 695,1525"/>
    <polyline points="121,1598 121,1879 318,1879"/>
    <line x1="0" y1="2138" x2="525" y2="2138"/>
    <line x1="740" y1="2138" x2="1200" y2="2138"/>
  </svg>

  <h1 class="page-title">KIDS MENU</h1>

  <div class="doodle" style="left:163px;top:196px;width:259px;height:92px" role="img" aria-label="Line drawing of a steam train"></div>
  <div class="doodle" style="left:799px;top:200px;width:170px;height:70px" role="img" aria-label="Line drawing of a bicycle"></div>
  <div class="doodle" style="left:66px;top:270px;width:66px;height:90px" role="img" aria-label="Line drawing of a leafy sprig"></div>
  <div class="doodle" style="left:744px;top:650px;width:336px;height:86px" role="img" aria-label="Line drawings of a plum, a toy helicopter and a ball"></div>

  <div class="photo photo-burger" role="img" aria-label="Photo of cheesy bread sticks in a basket with a cup of tomato dip"></div>
  <section class="dish dish-burger">
    <h2 class="dish-name">Cheeseburgerb1 |</h2>
    <p class="dish-name-ar">تشيزبرجر</p>
    <p class="dish-note" style="margin-top:54px">Served with french fries<br>and apple juice<span class="price">25</span></p>
    <p class="dish-note-ar" style="margin-top:24px"><span class="line"><bdi>يقدم مع بطاطس مقلية</bdi></span><span class="line"><bdi>وعصير تفاح</bdi><span class="price">25</span></span></p>
  </section>

  <div class="doodle" style="left:86px;top:836px;width:92px;height:92px" role="img" aria-label="Line drawing of a pear"></div>
  <div class="doodle" style="left:80px;top:978px;width:68px;height:88px" role="img" aria-label="Line drawing of a pacifier"></div>
  <div class="doodle" style="left:430px;top:1124px;width:60px;height:82px" role="img" aria-label="Line drawing of an apple"></div>
  <section class="dish dish-pasta">
    <h2 class="dish-name">Spaghetti with<br>Tomato Sauce</h2>
    <p class="dish-name-ar">سباجيتي مع صوص الطماطم</p>
    <p class="dish-note" style="margin-top:36px">Served with appple juice<span class="price">19</span></p>
    <p class="dish-note-ar"><bdi>تقدم مع عصير تفاح</bdi><span class="price">19</span></p>
  </section>
  <div class="photo photo-pasta" role="img" aria-label="Photo of spaghetti with meat tomato sauce and garlic bread"></div>

  <div class="doodle" style="left:76px;top:1146px;width:116px;height:170px" role="img" aria-label="Line drawing of a balloon with a curly string trailing down"></div>
  <div class="doodle" style="left:344px;top:1278px;width:370px;height:100px" role="img" aria-label="Line drawings of sugar cubes, a lemon slice and a pear"></div>

  <div class="photo photo-tenders" role="img" aria-label="Photo of chicken tenders with french fries in a basket"></div>
  <section class="dish dish-tenders">
    <h2 class="dish-name">Chicken Tenders Basketc</h2>
    <p class="dish-name-ar">تشيكن تندرز باسكت</p>
    <p class="dish-note" style="margin-top:50px">Served with french fries<br>and apple juice<span class="price">24</span></p>
    <p class="dish-note-ar" style="margin-top:24px"><span class="line"><bdi>تقدم مع بطاطس مقلية</bdi></span><span class="line"><bdi>وعصير تفاح</bdi><span class="price">24</span></span></p>
  </section>

  <div class="doodle" style="left:120px;top:2040px;width:360px;height:96px" role="img" aria-label="Line drawings of a tomato, a mushroom and a pomegranate"></div>
  <div class="doodle" style="left:550px;top:1970px;width:166px;height:180px" role="img" aria-label="Line drawing of a teddy bear"></div>
  <div class="doodle" style="left:810px;top:2034px;width:270px;height:100px" role="img" aria-label="Line drawings of a plum, an apple and a pear"></div>
</main>
</body>
</html>
```